Business Card Design

I am an Event and Wedding Planner in need of an eye catching business card featuring my logo (attached), my contact details, and my company tagline (Making every celebration glow with wonder...) I would like the tagline in font similar the logo's font.
Updates
I have just noticed that my logo has a misspelling so for the final design, I will be uploading a corrected logo as soon as I have it.
My apologies.
Reason: Waiting on a corrected logo...Lantern is misspelled and it should say Weddings not Wedding
The logo has been corrected so now Lantern is spelled correctly and it says Weddings instead of Wedding. Please use Edwardian Script ITC as the font for the tagline so it will match the logo. Thank you for your patience.
Target Market(s)
Engaged couples and people hosting milestone celebrations. 25-50 years old, predominately female
Industry/Entity Type
Business
Contact Information for Business Card
Rosalind Merrow, Event Manager / Owner, Mobile: 0491 868 254, Email: rosalind@velvetlanternco.com.au, www.velvetlanternco.com.au, Making every celebration glow with wonder...

```html
<!DOCTYPE html>
<html lang="en">
<head>
<meta charset="utf-8">
<title>Velvet Lantern Co – Business Card</title>
<link rel="stylesheet" href="https://fonts.googleapis.com/css2?family=Pinyon+Script&family=Arimo:wght@400&family=Tinos:ital@1&display=swap">
<style>
  :root {
    --page-bg: #d9d9d9;
    --card-bg: #ffffff;
    --ink: #1a1a1a;
    --ink-soft: #3a3a3a;
    --accent-red: #c0141c;
    --rule-grey: #444444;
  }
  * { margin: 0; padding: 0; box-sizing: border-box; }
  html, body {
    width: 1200px;
    height: 1000px;
    overflow: hidden;
    background: var(--page-bg);
  }
  .canvas {
    position: relative;
    width: 1200px;
    height: 1000px;
  }
  .card {
    position: absolute;
    width: 680px;
    height: 420px;
    background: var(--card-bg);
    border-radius: 16px;
  }
  .card--front { left: 100px; top: 60px; }
  .card--back { left: 330px; top: 500px; width: 700px; height: 440px; }

  /* Front */
  .brand {
    position: absolute;
    left: 0; right: 0;
    top: 150px;
    text-align: center;
    font-family: "Arimo", Arial, sans-serif;
    color: var(--ink-soft);
  }
  .brand__lockup {
    display: inline-flex;
    align-items: center;
    gap: 16px;
  }
  .brand__name {
    font-size: 44px;
    line-height: 1;
  }
  .brand__mark {
    width: 34px;
    height: 34px;
    border-radius: 50%;
    background: var(--accent-red);
    flex: none;
  }
  .brand__rule {
    width: 344px;
    height: 2px;
    margin: 28px auto 16px;
    background: var(--rule-grey);
  }
  .brand__descriptor {
    font-size: 26px;
    line-height: 1;
  }
  .tagline-rule {
    position: absolute;
    left: 110px;
    width: 500px;
    top: 350px;
    height: 1px;
    background: linear-gradient(90deg, rgba(192,20,28,0), var(--accent-red) 50%, rgba(192,20,28,0));
  }
  .tagline {
    position: absolute;
    left: 0; right: 0;
    top: 360px;
    text-align: center;
    font-family: "Pinyon Script", cursive;
    font-size: 24px;
    color: var(--accent-red);
  }

  /* Back */
  .person {
    position: absolute;
    left: 20px;
    top: 38px;
  }
  .person__name {
    font-family: "Arimo", Arial, sans-serif;
    font-size: 17px;
    text-transform: uppercase;
    color: var(--accent-red);
    letter-spacing: 0.2px;
  }
  .person__role {
    font-family: "Tinos", "Times New Roman", serif;
    font-style: italic;
    font-size: 14px;
    color: var(--ink);
    margin-top: 1px;
  }
  .contact-list {
    position: absolute;
    left: 24px;
    top: 148px;
    list-style: none;
  }
  .contact-list__item {
    display: flex;
    align-items: center;
    height: 32px;
    font-family: "Arimo", Arial, sans-serif;
    font-size: 17px;
    color: var(--ink);
  }
  .contact-list__icon {
    width: 26px;
    height: 22px;
    margin-right: 14px;
    flex: none;
  }
  .back-brand {
    position: absolute;
    right: 40px;
    top: 200px;
    width: 220px;
    display: flex;
    flex-direction: column;
    align-items: center;
    gap: 16px;
    font-family: "Arimo", Arial, sans-serif;
    font-size: 20px;
    color: var(--accent-red);
  }
  .back-brand__mark {
    width: 130px;
    height: 130px;
    border-radius: 50%;
    background: var(--accent-red);
  }
</style>
</head>
<body>
<main class="canvas">

  <section class="card card--front" aria-label="Business card front">
    <div class="brand">
      <div class="brand__lockup">
        <span class="brand__name">Velvet Lantern Co</span>
        <span class="brand__mark" aria-hidden="true"></span>
      </div>
      <div class="brand__rule"></div>
      <div class="brand__descriptor">Weddings and Events</div>
    </div>
    <div class="tagline-rule"></div>
    <p class="tagline">Making every celebration glow with wonder...</p>
  </section>

  <section class="card card--back" aria-label="Business card back">
    <div class="person">
      <p class="person__name">Rosalind Merrow</p>
      <p class="person__role">Event Manager / Owner</p>
    </div>
    <ul class="contact-list">
      <li class="contact-list__item">
        <svg class="contact-list__icon" viewBox="0 0 26 22" aria-hidden="true">
          <rect x="1" y="3" width="24" height="16" fill="var(--accent-red)"/>
          <polyline points="1,3 13,13 25,3" fill="none" stroke="#fff" stroke-width="1.8"/>
        </svg>
        rosalind@velvetlanternco.com.au
      </li>
      <li class="contact-list__item">
        <svg class="contact-list__icon" viewBox="0 0 26 22" aria-hidden="true">
          <rect x="7" y="0.5" width="12" height="21" rx="2.5" fill="var(--accent-red)"/>
          <rect x="9" y="3" width="8" height="13" fill="#fff"/>
          <circle cx="13" cy="18.5" r="1.3" fill="#fff"/>
        </svg>
        0491 868 254
      </li>
      <li class="contact-list__item">
        <svg class="contact-list__icon" viewBox="0 0 26 22" aria-hidden="true">
          <g fill="none" stroke="var(--accent-red)" stroke-width="1.6">
            <circle cx="13" cy="11" r="10"/>
            <ellipse cx="13" cy="11" rx="4.5" ry="10"/>
            <line x1="3" y1="11" x2="23" y2="11"/>
            <line x1="13" y1="1" x2="13" y2="21"/>
            <path d="M5 5.5 Q13 8.5 21 5.5 M5 16.5 Q13 13.5 21 16.5"/>
          </g>
        </svg>
        www.velvetlanternco.com.au
      </li>
    </ul>
    <div class="back-brand">
      <span class="back-brand__mark" aria-hidden="true"></span>
      <span class="back-brand__name">Velvet Lantern Co</span>
    </div>
  </section>

</main>
</body>
</html>
```